Business Card Design Project

I need a business card designed from scratch. I have an existing logo that I can upload in Illustrator for modification or redesign.

The Company is called Query Lanterns http://querylanterns.com.au and we provide Search Engine Optimization services to Australian businesses. The current logo signifies an increase in visitors, profits etc...

There are no restrictions as to the redesign - colours, style etc are all open to change.

Cards will be full colour and one sided printed at http://www.cardmoxel.com.au so check their requirements for file format and sizes etc.

I will expect all original files upon completion of project.

Target Market(s)

Any business with a web site looking to improve their search engine rankings

Industry/Entity Type

Business

Requirements
Must have
• I like modern, sleek designs. Clean, not fussy, uncluttered.

```html
<!DOCTYPE html>
<html lang="en">
<head>
<meta charset="utf-8">
<title>Query Lanterns — Business Cards</title>
<link rel="stylesheet" href="https://fonts.googleapis.com/css2?family=Source+Sans+3:wght@400;600;700&display=swap">
<style>
  :root {
    --backdrop: #a67c22;
    --card: #ffffff;
    --brand-blue: #0b6db5;
    --brand-yellow: #f2b51c;
    --ink: #222222;
    --band-yellow-start: #f3e25a;
    --band-yellow-end: #f6b318;
    --band-blue-start: #3b92d2;
    --band-blue-end: #1d3f66;
    --divider: #9a9a9a;
  }
  * { margin: 0; padding: 0; box-sizing: border-box; }
  html, body { width: 1200px; height: 686px; overflow: hidden; }
  body {
    background: var(--backdrop);
    font-family: "Source Sans 3", "Myriad Pro", Arial, sans-serif;
    position: relative;
  }
  .card {
    position: absolute;
    width: 510px;
    height: 291px;
    background: var(--card);
    border-radius: 14px;
    overflow: hidden;
    box-shadow: 1px 2px 4px rgba(0,0,0,0.45);
  }
  .card--front-a { left: 67px; top: 30px; }
  .card--front-b { left: 67px; top: 351px; }
  .card--back { left: 621px; top: 303px; }

  .brand {
    position: absolute;
    left: 0; right: 0;
    display: flex;
    align-items: center;
    justify-content: center;
    gap: 10px;
  }
  .brand__dot {
    width: 22px; height: 22px;
    border-radius: 50%;
    background: var(--brand-yellow);
  }
  .brand__name {
    font-weight: 700;
    font-size: 34px;
    color: var(--brand-blue);
    letter-spacing: 0.2px;
  }
  .card--front-a .brand { top: 64px; }
  .card--front-b .brand { top: 68px; }
  .card--back .brand { top: 120px; }

  .person { color: var(--brand-blue); font-weight: 700; font-size: 19px; }
  .person__title {
    color: var(--brand-yellow);
    font-weight: 600;
    font-size: 13px;
    border-left: 1px solid var(--brand-blue);
    padding-left: 8px;
    margin-left: 6px;
  }
  .line { font-size: 13px; color: var(--ink); display: flex; align-items: center; gap: 4px; }
  .icon { width: 11px; height: 11px; fill: var(--brand-blue); }

  /* Card A: centred stack */
  .stack { position: absolute; left: 0; right: 0; text-align: center; }
  .stack--name { top: 157px; display: flex; justify-content: center; align-items: baseline; }
  .stack--contact { top: 182px; display: flex; justify-content: center; gap: 20px; }
  .stack--address { top: 203px; font-size: 13px; color: var(--ink); }

  /* Card B: two columns */
  .col-left { position: absolute; right: 292px; top: 159px; text-align: right; }
  .col-left .person-row { display: flex; justify-content: flex-end; align-items: baseline; }
  .col-left .address { font-size: 13px; color: var(--ink); margin-top: 4px; }
  .col-divider {
    position: absolute; left: 233px; top: 157px;
    width: 1px; height: 51px;
    background: linear-gradient(to bottom, transparent, var(--divider), transparent);
  }
  .col-right { position: absolute; left: 246px; top: 166px; display: flex; flex-direction: column; gap: 4px; }

  /* Footer bands */
  .band-yellow {
    position: absolute; left: 0; bottom: 0;
    width: 290px; height: 17px;
    background: linear-gradient(to right, var(--band-yellow-start), var(--band-yellow-end));
    clip-path: polygon(0 0, 100% 0, calc(100% - 8px) 100%, 0 100%);
  }
  .band-blue {
    position: absolute; right: 0; bottom: 0;
    width: 232px; height: 28px;
    background: linear-gradient(to right, var(--band-blue-start), var(--band-blue-end));
    clip-path: polygon(12px 0, 100% 0, 100% 100%, 0 100%);
    display: flex; align-items: center; justify-content: flex-end;
    padding-right: 22px;
  }
  .band-blue__url { color: #ffffff; font-weight: 600; font-size: 13px; }
</style>
</head>
<body>

<svg width="0" height="0" style="position:absolute" aria-hidden="true">
  <symbol id="icon-phone" viewBox="0 0 24 24">
    <path d="M6.6 10.8a15.1 15.1 0 0 0 6.6 6.6l2.2-2.2a1 1 0 0 1 1-.25 11.4 11.4 0 0 0 3.6.57 1 1 0 0 1 1 1V20a1 1 0 0 1-1 1A17 17 0 0 1 3 4a1 1 0 0 1 1-1h3.5a1 1 0 0 1 1 1c0 1.25.2 2.45.57 3.57a1 1 0 0 1-.25 1z"/>
  </symbol>
  <symbol id="icon-mail" viewBox="0 0 24 24">
    <path d="M2 5h20v14H2z M2 5l10 7 10-7" />
  </symbol>
</svg>

<article class="card card--front-a">
  <div class="brand"><span class="brand__dot"></span><span class="brand__name">Query Lanterns</span></div>
  <div class="stack stack--name"><span class="person">Your Name</span><span class="person__title">Title</span></div>
  <div class="stack stack--contact">
    <span class="line"><svg class="icon"><use href="#icon-phone"/></svg>123-456-7890</span>
    <span class="line"><svg class="icon"><use href="#icon-mail"/></svg>inquiry@querylanterns.com.au.com</span>
  </div>
  <div class="stack stack--address">Street name City State, zip code</div>
  <div class="band-yellow"></div>
  <div class="band-blue"><span class="band-blue__url">www.querylanterns.com.au</span></div>
</article>

<article class="card card--front-b">
  <div class="brand"><span class="brand__dot"></span><span class="brand__name">Query Lanterns</span></div>
  <div class="col-left">
    <div class="person-row"><span class="person">Your Name</span><span class="person__title">Title</span></div>
    <div class="address">Street name City State, zip code</div>
  </div>
  <div class="col-divider"></div>
  <div class="col-right">
    <span class="line"><svg class="icon"><use href="#icon-phone"/></svg>123-456-7890</span>
    <span class="line"><svg class="icon"><use href="#icon-mail"/></svg>inquiry@querylanterns.com.au.com</span>
  </div>
  <div class="band-yellow"></div>
  <div class="band-blue"><span class="band-blue__url">www.querylanterns.com.au</span></div>
</article>

<article class="card card--back">
  <div class="brand"><span class="brand__dot"></span><span class="brand__name">Query Lanterns</span></div>
  <div class="band-yellow"></div>
  <div class="band-blue"><span class="band-blue__url">www.querylanterns.com.au</span></div>
</article>

</body>
</html>
```